Trendy eye catching business card for lawn mowing business

Turf Tidy, a local community lawn mowing service, requires an eye catching trendy business card to drop into letterboxes.

We could simply throw something together from a Microsoft Word template, but we are wanting something more than this. Some other business’ images are attached for some inspiration.

We are requiring the card to have Turf Tidy with our slogan, Call The Brindles. In addition, provide details with that we are a local, affordable lawn mowing service, and for other gardening matters to simply just ask!
Plus the relevant contact details, phone, email, social media.

Target Market(s)

Local community members who require assistance with their garden care

Industry/Entity Type

Gardening

Contact Information for Business Card

the name TURF TIDY is our logo
telephone logo 0438 215 967
email logo turftidy@postbox-mail.example
Instagram logo turftidy
Facebook logo turftidy.sth
Lawn Mowing Service
Local Affordable
edge trim, blow and clipping removal included.
Other gardening matters, just ask!

Font styles to use
Serif
Sans Serif
Decorative
Script

Colors
9bcb3c
ffffff

Requirements
Must have
• All the details listed in Business Card Details.
Make these words prominent:
Turf Tidy
Lawn Mowing Service
Local
Affordable
Nice to have
• Our slogan ‘Call The Brindles’ incorporated.
Different colour background for front and reverse side
Greens, white and black colours
Subtle grass blades images incorporated
Should not have
• No images of lawnmowers.
No images of men/cartoons.
No using initials for Turf Tidy

```html
<!DOCTYPE html>
<html lang="en">
<head>
<meta charset="utf-8">
<title>Turf Tidy – Business Card</title>
<link rel="stylesheet" href="https://fonts.googleapis.com/css2?family=Montserrat:wght@500;700;800&family=Arimo:wght@400;700&display=swap">
<style>
  :root {
    --lawn-green: #7dc242;
    --brand-green: #9bcb3c;
    --ink: #121212;
    --card-black: #101010;
    --paper: #ffffff;
    --slate: #6f6f6f;
    --rule: #8a8a8a;
    --backdrop: #d9dbd6;
  }
  * { box-sizing: border-box; margin: 0; padding: 0; }
  html, body {
    width: 1200px; height: 1015px; overflow: hidden;
    background: var(--backdrop);
  }
  .canvas {
    position: relative; width: 1200px; height: 1015px;
  }
  .card {
    position: absolute; left: 250px; width: 700px; height: 400px;
    overflow: hidden;
    box-shadow: 0 14px 30px rgba(0,0,0,.25);
  }
  /* ---------- front ---------- */
  .card--front { top: 60px; background: var(--card-black); color: var(--paper); }
  .card--front .accent-band {
    position: absolute; left: 0; right: 0; bottom: 0; height: 14px;
    background: var(--lawn-green);
  }
  .wordmark {
    position: absolute; top: 92px; left: 0; right: 0; text-align: center;
    font-family: "Montserrat", sans-serif; font-weight: 800;
    font-size: 64px; letter-spacing: 1px; line-height: 1;
    color: var(--lawn-green);
  }
  .slogan {
    position: absolute; left: 110px; right: 110px;
    display: flex; align-items: center; gap: 14px;
    font-family: "Montserrat", sans-serif; font-weight: 700;
    font-size: 21px; letter-spacing: 5px; color: var(--slate);
    white-space: nowrap;
  }
  .slogan::before, .slogan::after {
    content: ""; flex: 1; height: 1.5px; background: var(--rule);
  }
  .card--front .slogan { top: 168px; }
  .service {
    position: absolute; top: 222px; left: 0; right: 0; text-align: center;
  }
  .service__title {
    font-family: "Montserrat", sans-serif; font-weight: 800;
    font-size: 22px; letter-spacing: .5px;
  }
  .service__promise {
    font-family: "Arimo", sans-serif; font-size: 22px;
    color: var(--lawn-green); margin-top: 2px;
  }
  .service__details {
    font-family: "Arimo", sans-serif; font-size: 20px; line-height: 1.3;
    margin-top: 14px;
  }
  /* ---------- back ---------- */
  .card--back { top: 515px; background: var(--paper); color: var(--ink); }
  .grass-band {
    position: absolute; left: 0; bottom: 0; width: 700px; height: 400px;
  }
  .contacts {
    position: absolute; top: 38px; left: 360px;
    font-family: "Arimo", sans-serif; font-size: 19px; color: var(--ink);
    list-style: none;
  }
  .contacts li { display: flex; align-items: center; gap: 10px; height: 28px; }
  .contacts li.gap-before { margin-top: 16px; }
  .contacts svg { width: 22px; height: 22px; flex: none; }
  .logo-lockup {
    position: absolute; top: 150px; left: 60px; width: 300px;
  }
  .logo-lockup__name {
    display: flex; align-items: center; gap: 12px;
    font-family: "Montserrat", sans-serif; font-weight: 800;
    font-size: 46px; line-height: 1; color: var(--ink);
  }
  .logo-lockup__mark {
    width: 34px; height: 34px; background: var(--lawn-green); flex: none;
  }
  .card--back .slogan {
    position: static; margin-top: 10px; font-size: 15px; letter-spacing: 3.5px;
  }
</style>
</head>
<body>
<main class="canvas">

  <section class="card card--front" aria-label="Card front">
    <h1 class="wordmark">TURF TIDY</h1>
    <p class="slogan">CALL THE BRINDLES</p>
    <div class="service">
      <p class="service__title">LAWN MOWING SERVICE</p>
      <p class="service__promise">Local. Affordable.</p>
      <p class="service__details">Edge trim, blow and clipping removal included.<br>Other gardening matters, just ask!</p>
    </div>
    <div class="accent-band"></div>
  </section>

  <section class="card card--back" aria-label="Card back">
    <svg class="grass-band" viewBox="0 0 700 400" role="img" aria-label="Green grass blades rising along the bottom edge of the card">
      <defs>
        <linearGradient id="grassFade" x1="0" y1="1" x2="0" y2="0">
          <stop offset="0" stop-color="#7dc242"/>
          <stop offset="1" stop-color="#9bcb3c" stop-opacity=".75"/>
        </linearGradient>
      </defs>
      <path d="M0 400 L0 360 C120 340 220 330 330 300 C440 268 560 215 700 150 L700 400 Z" fill="url(#grassFade)"/>
    </svg>

    <ul class="contacts">
      <li>
        <svg viewBox="0 0 24 24" aria-hidden="true"><rect x="2" y="2" width="20" height="20" rx="4" fill="none" stroke="var(--lawn-green)" stroke-width="2"/><path d="M8 6l2 3-1.5 1.5c.8 1.8 2.2 3.2 4 4L14 13l3 2-1 2.5c-4.5-.3-8.2-4-8.5-8.5z" fill="var(--lawn-green)"/></svg>
        0438 215 967
      </li>
      <li>
        <svg viewBox="0 0 24 24" aria-hidden="true"><rect x="2" y="5" width="20" height="14" fill="var(--lawn-green)"/><path d="M2 5l10 8 10-8" fill="none" stroke="#fff" stroke-width="1.6"/></svg>
        turftidy@postbox-mail.example
      </li>
      <li class="gap-before">
        <svg viewBox="0 0 24 24" aria-hidden="true"><rect x="3" y="3" width="18" height="18" rx="4" fill="#c1358a"/></svg>
        photogram.example/turftidy
      </li>
      <li>
        <svg viewBox="0 0 24 24" aria-hidden="true"><circle cx="12" cy="12" r="10" fill="#3b5ba9"/></svg>
        friendbook.example/turftidy.com.au
      </li>
    </ul>

    <div class="logo-lockup">
      <p class="logo-lockup__name"><span class="logo-lockup__mark"></span>TURF TIDY</p>
      <p class="slogan">CALL THE BRINDLES</p>
    </div>
  </section>

</main>
</body>
</html>
```